skyPARLOR Helicopter Tour WordPress Website Design

SkyPARLOR (skyparlor-example.com) is a premium helicopter tour company offering scenic flights in two Florida cities: Tampa and Sarasota. We are seeking a full Wordpress website redesign that is modern, upbeat, inviting, and highly conversion‑focused. The new site should feel energetic and trustworthy, reflect the excitement of helicopter sightseeing, and maintain our recognizable SkyPARLOR color palette—while updating the overall look to feel fresh, clean, and current.
The website must be SEO‑friendly, mobile‑optimized, and easy to navigate. It should highlight our 5‑star customer reviews, showcase our tours clearly, and integrate seamlessly with TrailDock for instant online booking. The design should support a premium aviation experience while remaining friendly and accessible to tourists, families, couples, and adventure seekers.

These elements are essential and must be included in the design:

Brand & UX:
- Modern, upbeat, inviting design
- SEO‑friendly structure and layout
- Easy navigation and clear user flow
- Light grey “SP” background logo watermark (as used on current site)
- Clean, aviation‑inspired typography and layout

Conversion Features:
- Instant booking above the fold (TrailDock integration)
- Live Orbin Ratings carousel
- Tour comparison table (duration, route, price, etc.)
- FAQ expandable section
- Gift Cards page (highlighted as a major offering)
- What to Expect timeline (Arrive → Check‑In → Safety Briefing → Flight → Photos)
- Weather transparency widget (clear messaging about weather‑dependent flights

Content Structure:
- Separate pages for Tampa, Sarasota, and Gender Reveal Flights
- Pilot/Team profiles with short bios
- Highlighted features:
- Doors‑Off option
- Sunset flights
- Romantic packages
- Champagne add‑ons

Colors:
Use the existing SkyPARLOR palette as the foundation, but modernize it.
- Background: Clean with the light grey “SP” watermark integrated tastefully.
The overall color direction should feel bright, premium, energetic, and trustworthy

Target Market(s)

Tourists visiting Tampa or Sarasota, Families looking for memorable activities, Couples seeking romantic experiences (sunset flights, proposals, anniversaries), Adventure seekers and content creators, Locals celebrating birthdays, holidays, or special occasions, Gender reveal clients looking for a unique aerial reveal experience

Industry/Entity Type

Travel & Tourism / Aviation / Helicopter Tours / Experience‑based Activities

Requirements
Must have
• These elements are essential and must be included in the design: Brand & UX - Modern, upbeat, inviting design / SEO‑friendly structure and layout / Easy navigation and clear user flow / Light grey “SP” background logo watermark (as used on current site) / Clean, aviation‑inspired typography and layout
Nice to have
• Interactive route map showing flight paths / Subtle motion or parallax effects in hero sections / Animated icons or micro‑interactions / Social media integration (Instagram grid, TikTok clips) / Sticky mobile booking bar / Video header or short aerial footage loop / Subtle aviation‑themed graphic elements (rotor blur, sky gradients, etc.
Should not have
• No dark, heavy, or overly moody themes / No outdated fonts or overly playful typography / No cluttered layouts or excessive text blocks / No stocky, generic tourism imagery / No slow‑loading animations or heavy effects that hurt SEO

```html
<!DOCTYPE html>
<html lang="en">
<head>
<meta charset="utf-8">
<title>SkyPARLOR Helicopter Tours</title>
<link rel="stylesheet" href="https://fonts.googleapis.com/css2?family=Prata&family=Questrial&display=swap">
<style>
:root{
  --blue:#1f72ba;
  --blue-dark:#17609f;
  --orange:#f08a0c;
  --orange-light:#f8a424;
  --ink:#2e3338;
  --muted:#5f666d;
  --line:#e3e6ea;
  --soft:#eaf3fa;
  --green:#3b9c3c;
  --hex:#bcd3e9;
  --white:#fff;
}
*{box-sizing:border-box;margin:0;padding:0}
html,body{width:1200px;height:4274px;overflow:hidden}
body{font-family:"Questrial",sans-serif;color:var(--ink);background:var(--white);position:relative}
.serif{font-family:"Prata",serif;font-weight:400}
.abs{position:absolute}
.btn{display:inline-flex;align-items:center;justify-content:center;gap:7px;border-radius:30px;font-size:12px;letter-spacing:.3px;text-transform:uppercase;color:#fff;background:linear-gradient(180deg,var(--orange-light),var(--orange));}
.btn svg{width:12px;height:12px}
.btn-blue{background:var(--blue)}
.btn-outline{background:#fff;color:var(--orange);border:1.5px solid var(--orange)}
.section-title{position:absolute;left:0;width:1200px;text-align:center;font-family:"Prata",serif;color:var(--blue);font-size:35px;letter-spacing:.5px}
.section-sub{position:absolute;left:0;width:1200px;text-align:center;font-size:12.5px;color:var(--ink)}

/* header */
.site-header{top:0;left:0;width:1200px;height:102px;background:#fff}
.logo{display:flex;align-items:center;gap:8px;font-size:22px;color:var(--blue)}
.logo i{width:14px;height:14px;border-radius:50%;background:var(--blue);display:block}
.nav{top:40px;left:342px;display:flex;gap:22px;font-size:12px;color:var(--ink)}

/* hero */
.hero{top:102px;left:0;width:1200px;height:621px;overflow:hidden}
.hero-photo{position:absolute;inset:0;background:linear-gradient(100deg,#3b4a57 0%,#6d7c86 35%,#8f9a9c 55%,#5d6f7a 75%,#2f3e4b 100%)}
.hero-shade{position:absolute;inset:0;background:linear-gradient(90deg,rgba(20,30,40,.55),rgba(20,30,40,.15) 55%,rgba(0,0,0,0))}
.badge{top:83px;left:141px;width:272px;height:37px;border-radius:20px;background:rgba(40,40,40,.7);color:#fff;font-size:13px;display:flex;align-items:center;gap:8px;padding-left:22px}
.stars{display:flex;gap:2px}
.stars svg{width:15px;height:15px}
.hero h1{top:128px;left:141px;color:#fff;font-size:48px;line-height:56px}
.hero-text{top:247px;left:141px;width:450px;color:#fff;font-size:14px;line-height:24px}
.hero .stat{color:#fff}
.stat b{display:block;font-size:28px;font-weight:400}
.stat span{font-size:13px}

/* booking */
.booking{top:643px;left:106px;width:988px;height:177px;background:#fff;border-radius:6px;box-shadow:0 6px 24px rgba(0,0,0,.08)}
.booking h2{position:absolute;top:33px;left:0;width:100%;text-align:center;color:var(--blue);font-size:21px}
.field{position:absolute;top:82px}
.field label{display:block;font-size:11.5px;margin-bottom:9px}
.field .input{height:37px;border:1px solid var(--line);border-radius:4px;font-size:11.5px;color:var(--muted);display:flex;align-items:center;justify-content:space-between;padding:0 14px 0 16px}
.input svg{width:11px;height:11px}

/* tours */
.tour-card{top:995px;width:291px;height:494px;border:1px solid var(--line);border-radius:8px;overflow:hidden;background:#fff}
.tour-photo{height:188px}
.tour-body{padding:17px 18px}
.tour-body h3{font-size:17px;margin-bottom:8px}
.meta{display:flex;justify-content:space-between;font-size:11px;margin-bottom:12px}
.meta span{display:flex;align-items:center;gap:4px}
.meta svg{width:11px;height:11px}
.tour-body p{font-size:11.5px;line-height:20px;margin-bottom:10px}
.ticks{list-style:none}
.ticks li{display:flex;align-items:center;gap:8px;font-size:12.5px;margin-bottom:11px}
.ticks svg{width:17px;height:17px}
.price-row{position:absolute;bottom:44px;left:18px;right:18px;display:flex;justify-content:space-between;align-items:center}
.price{font-size:11.5px;line-height:16px}
.price b{font-weight:400;font-size:13.5px}
.arrow{width:56px;height:56px;border-radius:50%;display:flex;align-items:center;justify-content:center;background:#fff}

/* compare */
.compare{top:1580px;left:0;width:1200px;height:608px;background:#f2f4f6;overflow:hidden}
.compare-photo{position:absolute;right:0;top:0;width:520px;height:608px;background:radial-gradient(ellipse at 60% 35%,#e7d9d2 0%,#e9e4e2 35%,rgba(242,244,246,0) 70%)}
.compare table{position:absolute;top:178px;left:141px;width:917px;border-collapse:collapse;font-size:13.5px}
.compare th{background:var(--blue);color:#fff;height:54px;text-align:left;font-family:"Prata",serif;font-weight:400;font-size:17px}
.compare td{height:56.5px}
.compare tr:nth-child(odd) td{background:rgba(255,255,255,.92)}
.compare tr:nth-child(even) td{background:rgba(238,238,238,.92)}
.compare .btn{width:118px;height:34px;font-size:10.5px}
.tick-g{width:16px;height:16px}

/* expect */
.step{height:127px;background:#fff;filter:drop-shadow(0 6px 14px rgba(0,0,0,.08))}
.step-r{clip-path:polygon(0 0,94% 0,100% 50%,94% 100%,0 100%)}
.step-l{clip-path:polygon(6% 0,100% 0,100% 100%,6% 100%,0 50%)}
.step h3{font-size:18px;margin-bottom:12px;color:var(--ink)}
.step p{font-size:10.5px;line-height:20px}

/* reviews */
.reviews{top:2943px;left:0;width:1200px;height:440px;background:var(--soft)}
.review{top:177px;width:240px;height:166px;background:#fff;border-radius:4px;padding:18px 17px}
.review .who{display:flex;gap:10px;align-items:flex-start;margin-bottom:8px}
.avatar{width:26px;height:26px;border-radius:50%}
.who b{display:block;font-weight:400;font-size:11.5px}
.who small{font-size:10px;color:#888}
.review p{font-size:10px;line-height:16px;font-style:italic;color:#444;margin-top:6px}
.rstars{display:flex;gap:1px}
.rstars svg{width:13px;height:13px}

/* faq */
.faq-item{width:444px;background:#fff;border-radius:4px;box-shadow:0 3px 14px rgba(0,0,0,.07);font-size:12px;padding:0 17px}
.faq-q{height:48px;display:flex;align-items:center;justify-content:space-between}
.faq-ico{width:20px;height:20px;border-radius:50%;background:var(--blue);display:flex;align-items:center;justify-content:center}
.faq-ico svg{width:10px;height:10px}
.faq-a{font-size:12px;line-height:23px;color:#444;padding:14px 0 18px;border-top:1px solid var(--line)}

/* footer */
.footer{top:3900px;left:0;width:1200px;height:374px;background:var(--blue);color:#fff}
.footer h4{font-family:"Prata",serif;font-weight:400;font-size:16px;border-left:3px solid var(--orange);padding-left:9px;line-height:18px}
.footer p,.footer li{font-size:11.5px;line-height:24px}
.footer ul{list-style:none}
.contact-row{display:flex;gap:12px;margin-bottom:10px;font-size:11.5px;line-height:19px}
.contact-row svg{width:13px;height:13px;margin-top:3px;flex:none}
.social{display:flex;gap:9px}
.social i{width:26px;height:26px;border-radius:50%;border:1.5px solid #fff;display:block}
.social i:first-child{background:var(--orange);border-color:var(--orange)}
</style>
</head>
<body>

<svg width="0" height="0" style="position:absolute">
  <defs>
    <symbol id="star" viewBox="0 0 20 20"><path fill="#f6a21b" d="M10 1l2.7 5.8 6.3.7-4.7 4.3 1.3 6.2L10 14.9 4.4 18l1.3-6.2L1 7.5l6.3-.7z"/></symbol>
    <symbol id="cal" viewBox="0 0 16 16"><g fill="none" stroke="currentColor" stroke-width="1.6"><rect x="2" y="3" width="12" height="11" rx="1.5"/><path d="M2 7h12M5 1.5v3M11 1.5v3"/></g></symbol>
    <symbol id="tick" viewBox="0 0 20 20"><circle cx="10" cy="10" r="8.5" fill="none" stroke="#3b9c3c" stroke-width="1.6"/><path d="M6 10.3l2.7 2.7L14.3 7" fill="none" stroke="#3b9c3c" stroke-width="1.8"/></symbol>
    <symbol id="clock" viewBox="0 0 16 16"><circle cx="8" cy="8" r="6.5" fill="none" stroke="#2e3338" stroke-width="1.8"/><path d="M8 4.5V8l2.5 1.5" fill="none" stroke="#2e3338" stroke-width="1.6"/></symbol>
    <symbol id="people" viewBox="0 0 16 16"><g fill="#2e3338"><circle cx="6" cy="5" r="3"/><path d="M0.5 15c0-3.5 2.5-5.5 5.5-5.5s5.5 2 5.5 5.5z"/><circle cx="11.5" cy="5" r="2.3"/><path d="M12 9.5c2 .3 3.5 2 3.5 5.5h-3c0-2.3-.2-4-1.5-5.2z"/></g></symbol>
    <symbol id="chev" viewBox="0 0 10 10"><path d="M2 3.5l3 3 3-3" fill="none" stroke="#fff" stroke-width="1.8"/></symbol>
  </defs>
</svg>

<!-- header -->
<header class="site-header abs">
  <div class="logo abs" style="top:38px;left:141px"><i></i>skyPARLOR</div>
  <nav class="nav abs">
    <span>TOURS</span><span>TAMPA</span><span>SARASOTA</span><span>GENDER REVEAL</span><span>GIFT CARDS</span><span>ABOUT</span><span>CONTACT</span>
  </nav>
  <a class="btn abs" style="top:30px;left:914px;width:144px;height:41px"><svg><use href="#cal"/></svg>Book Now</a>
</header>

<!-- hero -->
<section class="hero abs">
  <div class="hero-photo" role="img" aria-label="Smiling passenger with headset looking out of a helicopter over the Tampa skyline"></div>
  <div class="hero-shade"></div>
  <div class="badge abs"><span class="stars"><svg><use href="#star"/></svg><svg><use href="#star"/></svg><svg><use href="#star"/></svg><svg><use href="#star"/></svg><svg><use href="#star"/></svg></span>500+ 5-Star Reviews</div>
  <h1 class="serif abs">Experience Florida<br>From Above</h1>
  <p class="hero-text abs">Premium Helicopter Tours in Tampa &amp; Sarasota. Unforgettable aerial adventures for every occasion.</p>
  <a class="btn abs" style="top:321px;left:141px;width:189px;height:41px"><svg><use href="#cal"/></svg>Book Your Flight</a>
  <a class="btn abs" style="top:321px;left:342px;width:142px;height:41px;background:transparent;border:1.5px solid #fff"><svg viewBox="0 0 16 16"><circle cx="8" cy="8" r="6.5" fill="none" stroke="#fff" stroke-width="1.6"/><path d="M6.5 5l4 3-4 3z" fill="#fff"/></svg>View Tours</a>
  <div class="stat abs" style="top:402px;left:141px"><b>10K+</b><span>Happy Flyers</span></div>
  <div class="stat abs" style="top:402px;left:271px"><b>15+</b><span>Years Flying</span></div>
  <div class="stat abs" style="top:402px;left:395px"><b>100%</b><span>Safety Record</span></div>
</section>

<!-- booking -->
<section class="booking abs">
  <h2 class="serif">BOOK YOUR ADVENTURE</h2>
  <div class="field" style="left:35px;width:177px"><label>Location</label><div class="input">Tampa<svg><use href="#chev" style="color:#555"/><path d="M2 4l4 4 4-4" fill="none" stroke="#555" stroke-width="1.5"/></svg></div></div>
  <div class="field" style="left:227px;width:211px"><label>Tour Type</label><div class="input">Intro Flight (15 min) - $149<svg viewBox="0 0 12 12"><path d="M2 4l4 4 4-4" fill="none" stroke="#555" stroke-width="1.5"/></svg></div></div>
  <div class="field" style="left:454px;width:177px"><label>Date</label><div class="input">dd/dd/yyyy<svg style="color:#555"><use href="#cal"/></svg></div></div>
  <div class="field" style="left:648px;width:110px"><label>Passengers</label><div class="input">1<svg viewBox="0 0 12 12"><path d="M2 4l4 4 4-4" fill="none" stroke="#555" stroke-width="1.5"/></svg></div></div>
  <a class="btn abs" style="top:101px;left:773px;width:179px;height:38px">Check Availability</a>
</section>

<!-- tours -->
<h2 class="section-title" style="top:902px">MOST POPULAR TOURS</h2>
<p class="section-sub" style="top:955px">Choose your perfect aerial adventure from our carefully curated tour collection</p>

<div class="arrow abs" style="top:1156px;left:59px;border:1px solid #e2e2e2"><svg width="12" height="12" viewBox="0 0 12 12"><path d="M8 2L4 6l4 4" fill="none" stroke="#bbb" stroke-width="1.5"/></svg></div>
<div class="arrow abs" style="top:1156px;left:1085px;border:1.5px solid var(--blue)"><svg width="12" height="12" viewBox="0 0 12 12"><path d="M4 2l4 4-4 4" fill="none" stroke="#1f72ba" stroke-width="1.5"/></svg></div>

<article class="tour-card abs" style="left:141px">
  <div class="tour-photo" role="img" aria-label="Passengers inside a helicopter cockpit over the coastline" style="background:linear-gradient(160deg,#7fb4d8,#b9ccd3 50%,#4c6170)"></div>
  <div class="tour-body">
    <h3 class="serif">Intro Flight</h3>
    <div class="meta"><span><svg><use href="#clock"/></svg>30-45 min</span><span><svg><use href="#people"/></svg>Up to 3 passengers</span></div>
    <p>Perfect first-time experience with stunning coastline views and city highlights.</p>
    <ul class="ticks"><li><svg><use href="#tick"/></svg>Scenic coastline route</li><li><svg><use href="#tick"/></svg>Up to 3 passengers</li><li><svg><use href="#tick"/></svg>Digital photos included</li></ul>
  </div>
  <div class="price-row"><div class="price">From<br><b>$249</b>/person</div><a class="btn" style="width:134px;height:42px"><svg><use href="#cal"/></svg>Book Now</a></div>
</article>

<article class="tour-card abs" style="left:454px">
  <div class="tour-photo" role="img" aria-label="Two smiling passengers wearing headsets in a helicopter above downtown" style="background:linear-gradient(160deg,#5b6a73,#9aa8ae 50%,#6c7b83)"></div>
  <div class="tour-body">
    <h3 class="serif">City Explorer</h3>
    <div class="meta"><span><svg><use href="#clock"/></svg>45-60 min</span><span><svg><use href="#people"/></svg>Up to 3 passengers</span></div>
    <p>Extended tour covering downtown skyline, bridges, beaches, and iconic landmarks</p>
    <ul class="ticks"><li><svg><use href="#tick"/></svg>Full city skyline views</li><li><svg><use href="#tick"/></svg>Doors-off option available</li><li><svg><use href="#tick"/></svg>HD video recording</li></ul>
  </div>
  <div class="price-row"><div class="price">From<br><b>$299</b>/person</div><a class="btn btn-blue" style="width:134px;height:42px;margin-top:-8px"><svg><use href="#cal"/></svg>Book Now</a></div>
</article>

<article class="tour-card abs" style="left:768px">
  <div class="tour-photo" role="img" aria-label="Couple in a helicopter cabin at golden hour over the city" style="background:linear-gradient(160deg,#6b6a66,#a6a8a4 50%,#8aa2b4)"></div>
  <div class="tour-body">
    <h3 class="serif">Sunset Flight</h3>
    <div class="meta"><span><svg><use href="#clock"/></svg>30 min</span><span><svg><use href="#people"/></svg>Up to 4 passengers</span></div>
    <p>Magical golden hour experience with breathtaking sunset views over the Gulf.</p>
    <ul class="ticks"><li><svg><use href="#tick"/></svg>Golden hour timing</li><li><svg><use href="#tick"/></svg>Champagne available</li><li><svg><use href="#tick"/></svg>Premium photo package</li></ul>
  </div>
  <div class="price-row"><div class="price">From<br><b>$499</b>/person</div><a class="btn btn-blue" style="width:134px;height:42px;margin-top:-8px"><svg><use href="#cal"/></svg>Book Now</a></div>
</article>

<!-- compare -->
<section class="compare abs">
  <div class="compare-photo" role="img" aria-label="Faded photo of a smiling passenger wearing sunglasses"></div>
  <h2 class="section-title" style="top:82px">COMPARE OUR TOURS</h2>
  <p class="section-sub" style="top:139px">Find the perfect flight for your adventure</p>
  <table>
    <thead><tr><th style="padding-left:34px;width:217px">Tour</th><th style="width:125px">Duration</th><th style="width:203px">Route</th><th style="width:136px">Doors-Off</th><th style="width:91px">Price</th><th></th></tr></thead>
    <tbody>
      <tr><td style="padding-left:34px">Intro Flight</td><td>15 min</td><td>Coastline</td><td style="padding-left:2px"><svg class="tick-g" viewBox="0 0 16 16"><path d="M2 8.5l4 4L14 4" fill="none" stroke="#3b9c3c" stroke-width="1.8"/></svg></td><td>$149</td><td><a class="btn btn-outline"><svg><use href="#cal"/></svg>Book Now</a></td></tr>
      <tr><td style="padding-left:34px">City Explorer</td><td>25 min</td><td>Downtown + Coast</td><td style="padding-left:2px"><svg class="tick-g" viewBox="0 0 16 16"><path d="M2 8.5l4 4L14 4" fill="none" stroke="#3b9c3c" stroke-width="1.8"/></svg></td><td>$249</td><td><a class="btn"><svg><use href="#cal"/></svg>Book Now</a></td></tr>
      <tr><td style="padding-left:34px">Sunset Flight</td><td>30 min</td><td>Gulf + Beaches</td><td style="padding-left:2px"><svg class="tick-g" viewBox="0 0 16 16"><path d="M2 8.5l4 4L14 4" fill="none" stroke="#3b9c3c" stroke-width="1.8"/></svg></td><td>$349</td><td><a class="btn btn-outline"><svg><use href="#cal"/></svg>Book Now</a></td></tr>
      <tr><td style="padding-left:34px">Deluxe Tour</td><td>45 min</td><td>Complete Circuit</td><td style="padding-left:2px"><svg class="tick-g" viewBox="0 0 16 16"><path d="M2 8.5l4 4L14 4" fill="none" stroke="#3b9c3c" stroke-width="1.8"/></svg></td><td>$449</td><td><a class="btn btn-outline"><svg><use href="#cal"/></svg>Book Now</a></td></tr>
      <tr><td style="padding-left:34px">Romantic Package</td><td>45 min</td><td>Sunset + Champagne</td><td style="padding-left:2px"><svg class="tick-g" viewBox="0 0 16 16"><path d="M2 8.5l4 4L14 4" fill="none" stroke="#3b9c3c" stroke-width="1.8"/></svg></td><td>$549</td><td><a class="btn btn-outline"><svg><use href="#cal"/></svg>Book Now</a></td></tr>
    </tbody>
  </table>
</section>

<!-- what to expect -->
<h2 class="section-title" style="top:2270px">WHAT TO EXPECT</h2>
<p class="section-sub" style="top:2322px">From arrival to takeoff, here’s how your aerial adventure unfolds</p>

<div class="step step-r abs" style="top:2385px;left:700px;width:356px;padding:27px 0 0 56px"><h3 class="serif">Arrive</h3><p>Arrive at our helipad 15 minutes before your<br>scheduled flight. Free parking available.</p></div>
<div class="step step-l abs" style="top:2465px;left:144px;width:356px;padding:27px 52px 0 0;text-align:right"><h3 class="serif">Check-In</h3><p>Quick and easy check-in process. Our friendly team<br>will verify your booking and answer any questions.</p></div>
<div class="step step-r abs" style="top:2545px;left:700px;width:356px;padding:27px 0 0 56px"><h3 class="serif">Safety Briefing</h3><p>Your pilot will provide a comprehensive safety<br>briefing and explain helicopter operations.</p></div>
<div class="step step-l abs" style="top:2628px;left:144px;width:356px;padding:27px 52px 0 0;text-align:right"><h3 class="serif">Flight Time!</h3><p>Lift off and enjoy breathtaking aerial views of<br>Florida’s most stunning landscapes!</p></div>
<div class="step step-r abs" style="top:2710px;left:700px;width:356px;padding:27px 0 0 56px"><h3 class="serif">Photos &amp; Memories</h3><p>Receive your complimentary photos and video<br>to share your amazing experience!</p></div>

<svg class="abs" style="top:2360px;left:440px" width="330" height="500" viewBox="0 0 330 500">
  <g fill="#fff" stroke="#bcd3e9" stroke-width="14" stroke-linejoin="round">
    <polygon points="232,25 277,50 277,120 232,145 187,120 187,50"/>
    <polygon points="91,107 136,132 136,202 91,227 46,202 46,132"/>
    <polygon points="232,188 277,213 277,283 232,308 187,283 187,213"/>
    <polygon points="91,270 136,295 136,365 91,390 46,365 46,295"/>
    <polygon points="232,352 277,377 277,447 232,472 187,447 187,377"/>
  </g>
  <g fill="none" stroke="#1f72ba" stroke-width="2.4" stroke-linecap="round" stroke-linejoin="round">
    <!-- car -->
    <path d="M214 92l6-12h24l6 12M210 92h44v12h-44zM216 104v5M248 104v5" fill="#1f72ba" stroke="#1f72ba"/>
    <!-- checklist -->
    <rect x="75" y="149" width="26" height="34" rx="2"/>
    <path d="M80 157h4M88 157h9M80 166h4M88 166h9M80 175h4M88 175h5"/>
    <circle cx="104" cy="180" r="8" fill="#1f72ba"/><path d="M100 180l3 3 5-6" stroke="#fff"/>
    <!-- shield -->
    <path d="M232 226l16 6v12c0 10-7 17-16 21-9-4-16-11-16-21v-12z"/>
    <path d="M225 246l5 5 9-10"/>
    <!-- clock -->
    <circle cx="91" cy="330" r="20"/><circle cx="91" cy="330" r="15"/><path d="M91 320v10l6 4"/>
    <!-- camera -->
    <path d="M214 402h9l4-6h10l4 6h9v22h-36z" fill="#1f72ba"/>
    <circle cx="232" cy="413" r="7" stroke="#fff"/>
  </g>
</svg>

<!-- reviews -->
<section class="reviews abs">
  <h2 class="section-title" style="top:82px">WHAT OUR GUESTS SAY</h2>
  <p class="section-sub" style="top:136px">Rated 4.9/5 stars from over 500+ flights</p>
  <div class="abs" style="top:195px;left:141px">
    <div style="font-size:14px">EXCELLENT</div>
    <div class="rstars" style="margin:6px 0 10px"><svg style="width:18px;height:18px"><use href="#star"/></svg><svg style="width:18px;height:18px"><use href="#star"/></svg><svg style="width:18px;height:18px"><use href="#star"/></svg><svg style="width:18px;height:18px"><use href="#star"/></svg><svg style="width:18px;height:18px"><use href="#star"/></svg></div>
    <div style="font-size:12px">Based on 225 reviews</div>
    <div style="font-size:40px;color:var(--blue);margin-top:6px">Orbin</div>
  </div>
  <div class="abs" style="top:253px;left:308px;width:20px;height:20px;border-radius:50%;background:#fff;display:flex;align-items:center;justify-content:center"><svg width="8" height="8" viewBox="0 0 10 10"><path d="M7 1L3 5l4 4" fill="none" stroke="#999" stroke-width="1.5"/></svg></div>

  <div class="review abs" style="left:320px">
    <div class="who"><span class="avatar" style="background:#3a8bd0"></span><div><b>Rena Castillo</b><small>2 weeks ago</small></div></div>
    <div class="rstars"><svg><use href="#star"/></svg><svg><use href="#star"/></svg><svg><use href="#star"/></svg><svg><use href="#star"/></svg><svg><use href="#star"/></svg></div>
    <p>Such a great experience! My husband booked us the romantic flight as a surprise and it was absolutely adorable. Definitely need to have a good tour guide and I liked ours.</p>
  </div>
  <div class="review abs" style="left:570px">
    <div class="who"><span class="avatar" style="background:#3e7a2f"></span><div><b>Maris T</b><small>1 week ago</small></div></div>
    <div class="rstars"><svg><use href="#star"/></svg><svg><use href="#star"/></svg><svg><use href="#star"/></svg><svg><use href="#star"/></svg><svg><use href="#star"/></svg></div>
    <p>Great experience for a first timer! Marco was a great pilot and tour guide. Accommodated our schedule changes and easy to work with. Highly recommend!</p>
  </div>
  <div class="review abs" style="left:818px">
    <div class="who"><span class="avatar" style="background:#d86a3c"></span><div><b>Tomas Varela</b><small>2 weeks ago</small></div></div>
    <div class="rstars"><svg><use href="#star"/></svg><svg><use href="#star"/></svg><svg><use href="#star"/></svg><svg><use href="#star"/></svg><svg><use href="#star"/></svg></div>
    <p>This was an Early Christmas gift for my 9yr old special needs son. Everything exceeded my expectations and Marco our pilot did an amazing job. He was super friendly and made sure...</p>
  </div>
</section>

<!-- faq -->
<h2 class="section-title" style="top:3462px">FREQUENTLY ASKED QUESTIONS</h2>
<p class="section-sub" style="top:3516px">Everything you need to know before your flight</p>

<div class="faq-item abs" style="top:3566px;left:141px"><div class="faq-q">Lorem Ipsum is simply dummy text?<span class="faq-ico"><svg><use href="#chev"/></svg></span></div></div>
<div class="faq-item abs" style="top:3629px;left:141px"><div class="faq-q">Standard dummy text ever since the 1500s when?<span class="faq-ico"><svg><use href="#chev"/></svg></span></div></div>
<div class="faq-item abs" style="top:3692px;left:141px"><div class="faq-q">Printer took a galley of type and scrambled?<span class="faq-ico"><svg><use href="#chev"/></svg></span></div></div>
<div class="faq-item abs" style="top:3757px;left:141px"><div class="faq-q">Lectronic typesetting remaining unchanged?<span class="faq-ico"><svg><use href="#chev"/></svg></span></div></div>

<div class="faq-item abs" style="top:3566px;left:614px">
  <div class="faq-q">Lectronic typesetting remaining unchanged?<span class="faq-ico" style="background:var(--orange)"><svg viewBox="0 0 10 10"><path d="M2 6.5l3-3 3 3" fill="none" stroke="#fff" stroke-width="1.8"/></svg></span></div>
  <div class="faq-a">Lorem ipsum dolor sit amet, consectetuer adipiscing elit, sed diam nonummy nibh euismod tincidunt ut laoreet dolore magna aliquam erat volutpat. Ut wisi enim ad minim veniam, quis nostrud exerci tation ullamcorper suscipit.</div>
</div>
<div class="faq-item abs" style="top:3757px;left:614px"><div class="faq-q">Standard dummy text ever since the 1500s when?<span class="faq-ico"><svg><use href="#chev"/></svg></span></div></div>

<!-- footer -->
<footer class="footer abs">
  <div class="abs" style="top:67px;left:141px;width:230px">
    <h4>ABOUT SKYPARLOR</h4>
    <p style="margin-top:16px">Ut wisi enim ad minim veniam, quis nostrud exerci tation ullamcorper suscipit lobortis nisl ut aliquip ex ea commodo consequat.</p>
    <div class="social" style="margin-top:14px"><i></i><i></i><i></i><i></i></div>
  </div>
  <div class="abs" style="top:67px;left:422px;width:220px">
    <h4>CONTACT DETAILS</h4>
    <div style="margin-top:18px">
      <div class="contact-row"><svg viewBox="0 0 16 16"><path d="M4 1.5l2.5 3-1.5 2c1 2 2.5 3.5 4.5 4.5l2-1.5 3 2.5-1.5 2.5C7 14.5 1.5 9 1.5 3z" fill="#fff"/></svg><div>Phone<br>(800) 555-0142</div></div>
      <div class="contact-row"><svg viewBox="0 0 16 16"><rect x="1" y="3" width="14" height="10" rx="1" fill="#fff"/><path d="M1.5 4l6.5 5 6.5-5" fill="none" stroke="#1f72ba" stroke-width="1.4"/></svg><div>Email<br>info@skyparlor-example.com</div></div>
      <div class="contact-row"><svg viewBox="0 0 16 16"><circle cx="8" cy="8" r="6.5" fill="none" stroke="#fff" stroke-width="1.8"/><path d="M8 4.5V8l2.5 1.5" fill="none" stroke="#fff" stroke-width="1.6"/></svg><div>Opening Hours<br>Mon-Sat 9:00am - 5:30pm<br>Sun 10:00am - 3:00pm</div></div>
    </div>
  </div>
  <div class="abs" style="top:67px;left:680px">
    <h4 style="border:none;padding-left:0">QUICK LINKS</h4>
    <ul style="margin-top:14px"><li>• Tours</li><li>• Tampa</li><li>• Sarasota</li><li>• Gender Reveal</li><li>• Gift Cards</li><li>• About</li><li>• Contact</li></ul>
  </div>
  <div class="abs" style="top:102px;left:860px;width:198px;display:flex;align-items:center;gap:9px;font-size:28px"><i style="width:16px;height:16px;border-radius:50%;background:#fff;display:block"></i>skyPARLOR</div>
  <div class="abs" style="top:320px;left:141px;width:917px;border-top:1px solid rgba(255,255,255,.3)"></div>
  <p class="abs" style="top:338px;left:0;width:1200px;text-align:center;font-size:10.5px">© 2026 SkyPARLOR. All Rights Reserved.</p>
</footer>

</body>
</html>
```